BOLD & MINIMALIST DESIGN NEEDED

We want a very bold but minimalistic business card design that is impactful and utilizes both sides of the business card. Our current logo is included for your use.

We want bold fonts and good use of negative space. We don't want the logo to overpower the design.

Target Market(s)

Professionals who are building new commercial buildings.

Industry/Entity Type

Construction

Contact Information for Business Card

Name, Title, email, office phone, cell phone, website

Font styles to use
Serif
Sans Serif

Requirements
Must have
• Bold design!

```html
<!DOCTYPE html>
<html lang="en">
<head>
<meta charset="utf-8">
<title>Ridgeline Design + Build — Business Card</title>
<link rel="stylesheet" href="https://fonts.googleapis.com/css2?family=Montserrat:wght@400;500;600;800&display=swap">
<style>
  :root {
    --backdrop: #3b3b3d;
    --green: #86c440;
    --green-light: #a6d86c;
    --green-dark: #3f7a2f;
    --ink: #111111;
    --paper: #ffffff;
    --muted: #222222;
  }
  * { box-sizing: border-box; margin: 0; padding: 0; }
  html, body { width: 1200px; height: 689px; overflow: hidden; }
  body {
    background: var(--backdrop);
    font-family: "Montserrat", sans-serif;
    position: relative;
  }
  .card {
    position: absolute;
    top: 196px;
    width: 520px;
    height: 297px;
    border-radius: 18px;
    overflow: hidden;
  }
  /* Front side */
  .card--front {
    left: 50px;
    background: linear-gradient(120deg, var(--green-light) 0%, var(--green) 45%, var(--green) 100%);
    display: flex;
    align-items: center;
    justify-content: center;
  }
  .brand {
    color: var(--green-dark);
    font-weight: 800;
    text-align: center;
    line-height: 1;
  }
  .brand__name { display: block; font-size: 54px; letter-spacing: 1px; }
  .brand__tag { display: block; font-size: 16px; letter-spacing: 9px; margin-top: 10px; }

  /* Back side */
  .card--back { left: 630px; background: var(--paper); }
  .card__band { position: absolute; inset: 0; width: 100%; height: 100%; }
  .card--back .brand {
    position: absolute;
    left: 0; right: 0; top: 34px;
    color: var(--ink);
  }
  .card--back .brand__name { font-size: 38px; }
  .card--back .brand__tag { font-size: 11px; letter-spacing: 7px; margin-top: 6px; }

  .person {
    position: absolute;
    left: 34px;
    top: 142px;
    text-align: right;
    width: 200px;
  }
  .person__name { color: var(--green); font-weight: 800; font-size: 25px; letter-spacing: 0.5px; }
  .person__title { color: var(--muted); font-weight: 500; font-size: 12px; letter-spacing: 1px; margin-top: 4px; }

  .divider {
    position: absolute;
    left: 252px; top: 128px;
    width: 1.5px; height: 74px;
    background: #1b1b3a;
  }
  .contacts {
    position: absolute;
    left: 268px; top: 124px;
    list-style: none;
  }
  .contacts li {
    display: flex;
    align-items: center;
    gap: 7px;
    font-size: 12px;
    color: var(--muted);
    height: 20px;
  }
  .contacts svg { width: 11px; height: 11px; fill: var(--green); flex: none; }
  .address {
    position: absolute;
    right: 26px; bottom: 18px;
    color: var(--paper);
    font-size: 12px;
    font-weight: 500;
    letter-spacing: 0.3px;
  }
</style>
</head>
<body>

  <section class="card card--front" aria-label="Card front">
    <div class="brand">
      <span class="brand__name">RIDGELINE</span>
      <span class="brand__tag">DESIGN + BUILD</span>
    </div>
  </section>

  <section class="card card--back" aria-label="Card back">
    <svg class="card__band" viewBox="0 0 520 297" preserveAspectRatio="none" aria-hidden="true">
      <path d="M0,297 L0,262 Q300,258 520,140 L520,297 Z" fill="var(--green)"/>
      <path d="M40,252 Q310,238 500,130" fill="none" stroke="var(--ink)" stroke-width="3"/>
    </svg>

    <div class="brand">
      <span class="brand__name">RIDGELINE</span>
      <span class="brand__tag">DESIGN + BUILD</span>
    </div>

    <div class="person">
      <p class="person__name">MARCUS HALE</p>
      <p class="person__title">OWNER-CEO</p>
    </div>

    <div class="divider"></div>

    <ul class="contacts">
      <li><svg viewBox="0 0 24 24"><path d="M6.6 10.8a15 15 0 006.6 6.6l2.2-2.2a1 1 0 011-.25 11.4 11.4 0 003.6.57 1 1 0 011 1V20a1 1 0 01-1 1A17 17 0 013 4a1 1 0 011-1h3.5a1 1 0 011 1 11.4 11.4 0 00.57 3.6 1 1 0 01-.25 1z"/></svg>123 456 789</li>
      <li><svg viewBox="0 0 24 24"><path d="M7 1h10a2 2 0 012 2v18a2 2 0 01-2 2H7a2 2 0 01-2-2V3a2 2 0 012-2zm0 3v15h10V4zm5 16.2a1 1 0 100 .1z"/></svg>123 456 789</li>
      <li><svg viewBox="0 0 24 24"><path d="M2 5h20v14H2zm2 2v.5l8 5 8-5V7l-8 5z"/></svg>info@ridgelinebuild.com</li>
      <li><svg viewBox="0 0 24 24"><path d="M12 2a10 10 0 100 20 10 10 0 000-20zm6.9 6h-3a15 15 0 00-1.3-3.9A8 8 0 0118.9 8zM12 4a13 13 0 011.9 4h-3.8A13 13 0 0112 4zM4.3 14a8 8 0 010-4h3.4a16 16 0 000 4zm.8 2h3a15 15 0 001.3 3.9A8 8 0 015.1 16zm3-8h-3a8 8 0 014.3-3.9A15 15 0 008.1 8zM12 20a13 13 0 01-1.9-4h3.8A13 13 0 0112 20zm2.3-6H9.7a14 14 0 010-4h4.6a14 14 0 010 4zm.3 5.9a15 15 0 001.3-3.9h3a8 8 0 01-4.3 3.9zm1.7-5.9a16 16 0 000-4h3.4a8 8 0 010 4z"/></svg>www.ridgelinebuild.com</li>
    </ul>

    <p class="address">Your address, City State, Zip 1234</p>
  </section>

</body>
</html>
```